Business Card for a Dental Office

The design should communicate integrity, quality and reliability. We also want the card look elegant, simple, but still stand out, different from the traditional-dental-office business card.

Industry/Entity Type

Business

```html
<!DOCTYPE html>
<html lang="en">
<head>
<meta charset="utf-8">
<title>Harwell Dental Centre – Business Card</title>
<link rel="stylesheet" href="https://fonts.googleapis.com/css2?family=Open+Sans:ital,wdth,wght@0,75..100,400..700;1,75..100,400..700&display=swap">
<style>
  :root {
    --gold: #c9a61c;
    --gold-dark: #a8870f;
    --yellow: #f7ec1e;
    --ink: #111111;
    --paper: #ffffff;
    --backdrop: #e9e6e3;
  }
  * { box-sizing: border-box; margin: 0; padding: 0; }
  html, body { width: 1200px; height: 900px; overflow: hidden; }
  body {
    background: var(--backdrop);
    font-family: "Open Sans", Arial, sans-serif;
    color: var(--ink);
    position: relative;
  }
  .card {
    position: absolute;
    background: var(--paper);
    overflow: hidden;
    box-shadow: 0 4px 14px rgba(0,0,0,.18);
    text-align: center;
  }
  .card--front { left: 65px; top: 42px; width: 607px; height: 371px; }
  .card--back  { left: 388px; top: 506px; width: 567px; height: 351px; }

  .card__swoosh { position: absolute; left: 0; bottom: 0; width: 100%; height: 100px; display: block; }

  .person__name { margin-top: 34px; font-size: 22px; font-weight: 600; color: var(--gold); letter-spacing: .5px; line-height: 1.1; }
  .person__role { font-size: 16px; margin-top: 3px; }

  .brand { display: flex; align-items: center; justify-content: center; gap: 8px; }
  .brand__mark { width: 34px; height: 34px; background: var(--gold); }
  .brand__text { text-align: left; }
  .brand__name {
    display: block; font-weight: 700; font-stretch: 75%;
    font-size: 31px; letter-spacing: 0; text-transform: uppercase; line-height: 1;
  }
  .brand__tagline {
    display: block; font-size: 13px; font-weight: 600; color: var(--gold);
    letter-spacing: .9px; text-transform: uppercase; margin-top: 2px; line-height: 1.1;
  }
  .card--front .brand { margin-top: 60px; margin-left: -24px; }

  .contact { margin-top: 22px; font-size: 15.5px; line-height: 25px; }
  .contact__line { display: flex; align-items: center; justify-content: center; gap: 5px; }
  .contact__icon { width: 12px; height: 12px; }

  .card__footer {
    position: absolute; left: 0; bottom: 0; width: 100%; height: 70px;
    display: flex; align-items: center; justify-content: center; padding-top: 8px;
    font-size: 15.5px;
  }

  .appointment__title { margin-top: 26px; font-size: 21px; font-weight: 600; color: var(--gold); }
  .card--back .brand { margin-top: 16px; }
  .card--back .brand__text { text-align: center; }
  .card--back .brand__name { font-size: 27px; }
  .card--back .brand__tagline { font-size: 11.5px; margin-top: 2px; }

  .form { margin: 30px 82px 0; text-align: left; font-size: 14px; font-weight: 600; }
  .form__row { display: flex; align-items: baseline; height: 41px; }
  .form__label { white-space: nowrap; margin-right: 6px; }
  .form__dots { flex: 1; border-bottom: 2px dotted var(--ink); height: 1px; transform: translateY(-3px); }
  .form__unit { margin: 0 6px; }

  .card--back .card__footer { font-style: italic; font-weight: 600; font-size: 15.5px; height: 56px; }
</style>
</head>
<body>

<section class="card card--front" aria-label="Business card front">
  <p class="person__name">DANIEL HART</p>
  <p class="person__role">Managing Direcator</p>

  <div class="brand">
    <span class="brand__mark"></span>
    <span class="brand__text">
      <span class="brand__name">Harwell Dental Centre</span>
      <span class="brand__tagline">A bright smile opens every door</span>
    </span>
  </div>

  <div class="contact">
    <p class="contact__line">
      <svg class="contact__icon" viewBox="0 0 24 24" aria-hidden="true"><path fill="#c9a61c" d="M6.6 10.8a15.1 15.1 0 0 0 6.6 6.6l2.2-2.2a1 1 0 0 1 1-.25 11.4 11.4 0 0 0 3.6.57 1 1 0 0 1 1 1V20a1 1 0 0 1-1 1A17 17 0 0 1 3 4a1 1 0 0 1 1-1h3.5a1 1 0 0 1 1 1c0 1.25.2 2.45.57 3.57a1 1 0 0 1-.25 1z"/></svg>
      555-214-3098
    </p>
    <p class="contact__line">
      <svg class="contact__icon" viewBox="0 0 24 24" aria-hidden="true"><path fill="#c9a61c" d="M2 5h20v14H2z"/><path fill="none" stroke="#fff" stroke-width="1.6" d="M2 5l10 8 10-8"/></svg>
      hello@harwelldental.com
    </p>
  </div>

  <svg class="card__swoosh" viewBox="0 0 607 100" preserveAspectRatio="none" aria-hidden="true">
    <defs>
      <linearGradient id="bandFront" x1="0" y1="0" x2="0" y2="1">
        <stop offset="0" stop-color="#c8a915"/>
        <stop offset=".45" stop-color="#f7ec1e"/>
        <stop offset="1" stop-color="#f3e21c"/>
      </linearGradient>
    </defs>
    <path d="M0 40 Q300 2 607 28 L607 100 L0 100 Z" fill="url(#bandFront)"/>
    <path d="M105 23 Q420 -12 607 26 L607 46 Q470 4 105 23 Z" fill="#111"/>
  </svg>
  <p class="card__footer">48, Maple Row Harwell Town, 204816</p>
</section>

<section class="card card--back" aria-label="Appointment card back">
  <p class="appointment__title">Your Next Appointment is</p>

  <div class="brand">
    <span class="brand__text">
      <span class="brand__name">Harwell Dental Centre</span>
      <span class="brand__tagline">A bright smile opens every door</span>
    </span>
  </div>

  <div class="form">
    <div class="form__row"><span class="form__label">Name :</span><span class="form__dots"></span></div>
    <div class="form__row"><span class="form__label">Date :</span><span class="form__dots"></span></div>
    <div class="form__row">
      <span class="form__label">Time :</span><span class="form__dots"></span>
      <span class="form__unit">AM</span><span class="form__dots"></span>
      <span class="form__unit">PM</span>
    </div>
  </div>

  <svg class="card__swoosh" viewBox="0 0 567 100" preserveAspectRatio="none" aria-hidden="true">
    <defs>
      <linearGradient id="bandBack" x1="0" y1="0" x2="0" y2="1">
        <stop offset="0" stop-color="#c8a915"/>
        <stop offset=".45" stop-color="#f7ec1e"/>
        <stop offset="1" stop-color="#f3e21c"/>
      </linearGradient>
    </defs>
    <path d="M0 52 Q260 12 567 44 L567 100 L0 100 Z" fill="url(#bandBack)"/>
    <path d="M0 38 Q230 -8 470 22 Q250 8 0 56 Z" fill="#111"/>
  </svg>
  <p class="card__footer">If unable to keep appointment, kindly give 24hrs notice.</p>
</section>

</body>
</html>
```